Pepper & Palm Business Card FUN & EXCITING

Here is the Information for the Card:
Jaswinder Bains (Ravi)
E: RaviBains@postlark.com
C: (480) 555-0147
www.PepperPalmLV.com

We don't want traditional Indian cliche, We a playful bold and fun business card.

Files: https://files.cloudvessel.net/share/folders/7TqRmXpZ2vKa9LwBn4YcHd3JsEf6UoGi?usp=share_link

https://files.cloudvessel.net/share/folders/4MzXaQ8rTw2YbNcVk6PsLe5GhJdR3FoU?usp=share_link

Target Market(s)

Las Vegas Local Restaurant

Industry/Entity Type

Indian Restaurant

Contact Information for Business Card

Name, Email, Cell Phone, Company Logo

```html
<!DOCTYPE html>
<html lang="en">
<head>
<meta charset="utf-8">
<title>Pepper &amp; Palm — Business Card</title>
<link rel="stylesheet" href="https://fonts.googleapis.com/css2?family=Montserrat:wght@400;600;800&display=swap">
<style>
  :root {
    --backdrop: #2a2a2a;
    --card: #1e1e1e;
    --ink-white: #ffffff;
    --ink-soft: #e8e8e8;
    --ink-muted: #4a4a4a;
    --accent-orange: #ee7a26;
    --accent-pink: #de6588;
  }
  * { margin: 0; padding: 0; box-sizing: border-box; }
  html, body {
    width: 1200px; height: 1108px; overflow: hidden;
    background: var(--backdrop);
    font-family: "Montserrat", sans-serif;
  }
  .canvas { position: relative; width: 1200px; height: 1108px; }
  .card {
    position: absolute; left: 257px; width: 698px;
    background: var(--card); border-radius: 18px; overflow: hidden;
  }
  .card--front { top: 126px; height: 428px; }
  .card--back { top: 594px; height: 440px; }

  .brand {
    position: absolute; left: 0; right: 0; text-align: center;
    font-weight: 800; letter-spacing: -0.5px; line-height: 1;
  }
  .brand__name { font-size: 46px; }
  .brand__place { font-size: 14px; font-weight: 800; margin-top: 8px; }
  .card--front .brand { top: 172px; color: var(--ink-muted); }
  .card--back .brand { top: 60px; color: var(--ink-white); }

  .holder {
    position: absolute; right: 350px; top: 282px; text-align: right;
  }
  .holder__name { font-size: 26px; font-weight: 600; color: var(--accent-orange); }
  .holder__role { font-size: 16px; color: var(--ink-soft); margin-top: 2px; }

  .divider {
    position: absolute; left: 364px; top: 270px; width: 2px; height: 82px;
    background: var(--accent-orange);
  }
  .contacts { position: absolute; left: 380px; top: 268px; list-style: none; }
  .contacts__item {
    display: flex; align-items: center; height: 29px;
    font-size: 16px; color: var(--ink-soft);
  }
  .contacts__icon { width: 14px; height: 14px; margin-right: 15px; fill: var(--accent-orange); }

  .stripe { position: absolute; left: 0; bottom: 0; width: 698px; height: 14px; }
</style>
</head>
<body>
<main class="canvas">
  <section class="card card--front">
    <div class="brand">
      <div class="brand__name">Pepper &amp; Palm</div>
      <div class="brand__place">Las Vegas, NV</div>
    </div>
  </section>

  <section class="card card--back">
    <div class="brand">
      <div class="brand__name">Pepper &amp; Palm</div>
      <div class="brand__place">Las Vegas, NV</div>
    </div>

    <div class="holder">
      <div class="holder__name">Jaswinder Bains (Ravi)</div>
      <div class="holder__role">owner</div>
    </div>

    <div class="divider"></div>

    <ul class="contacts">
      <li class="contacts__item">
        <svg class="contacts__icon" viewBox="0 0 16 16" aria-hidden="true"><path d="M1 6c0-2 3-4 7-4s7 2 7 4v1h-3V5.5H4V7H1zM3 8h10l1 6H2z"/></svg>
        (480) 555-0147
      </li>
      <li class="contacts__item">
        <svg class="contacts__icon" viewBox="0 0 16 16" aria-hidden="true"><path d="M1 3h14v2L8 9 1 5zM1 7l7 4 7-4v6H1z"/></svg>
        RaviBains@postlark.com
      </li>
      <li class="contacts__item">
        <svg class="contacts__icon" viewBox="0 0 16 16" aria-hidden="true"><circle cx="8" cy="8" r="7"/></svg>
        www.PepperPalmLV.com
      </li>
    </ul>

    <svg class="stripe" viewBox="0 0 698 14" aria-hidden="true">
      <polygon points="0,0 240,0 232,14 0,14" fill="#ee7a26"/>
      <polygon points="243,0 484,0 476,14 235,14" fill="#de6588"/>
      <polygon points="487,0 698,0 698,14 479,14" fill="#ffffff"/>
    </svg>
  </section>
</main>
</body>
</html>
```